Valentines Day Helicopter Tour Mailer

The purpose behind this project is to design a mailer for helicopter tours around valentines day. Not sure exaclty all what to include as i'm not sure if i want to price on it yet but i want helicopters, hearts, and something interesting to draw attention to the service we will be offering. If we did include price it would be $169/ person. Size should be good for 8.5 by 11 paper

general public

```html
<!DOCTYPE html>
<html lang="en">
<head>
<meta charset="utf-8">
<title>Valentine's Helicopter Tour Mailer</title>
<link rel="stylesheet" href="https://fonts.googleapis.com/css2?family=Oswald:wght@500;600&family=Chewy&family=Luckiest+Guy&family=Kaushan+Script&display=swap">
<style>
  :root {
    --backdrop: #d4d4d4;
    --night: #1b1a1c;
    --slate: #3a3a3c;
    --forest: #3b4a34;
    --river: #7c8a88;
    --rotor-black: #0e0e10;
    --fuselage: #2a2b2e;
    --magenta: #e6168b;
    --hot-pink: #ec0a8c;
    --violet: #9a2fd0;
    --deep-violet: #6d1ea8;
    --orchid: #c24bd8;
    --gold: #ffb21e;
    --amber: #ff8a10;
    --white: #ffffff;
  }
  * { margin: 0; padding: 0; box-sizing: border-box; }
  html, body { width: 1015px; height: 1200px; overflow: hidden; background: var(--backdrop); }
  .canvas { position: relative; width: 1015px; height: 1200px; }
  .mailer {
    position: absolute; left: 133px; top: 120px; width: 748px; height: 960px;
    overflow: hidden; font-family: "Oswald", sans-serif; color: var(--white);
  }
  .scene-photo {
    position: absolute; inset: 0;
    background:
      radial-gradient(ellipse 60% 30% at 75% 42%, rgba(70,95,60,.9), transparent 70%),
      radial-gradient(ellipse 50% 22% at 80% 62%, rgba(150,165,160,.55), transparent 70%),
      linear-gradient(180deg, #141414 0%, var(--slate) 25%, var(--forest) 45%, var(--river) 62%, #4a4a4c 75%, var(--night) 100%);
  }
  .helicopter-photo {
    position: absolute; left: 0; top: 230px; width: 300px; height: 460px; z-index: 1;
    border-radius: 0 60% 40% 0 / 0 45% 55% 0;
    background:
      radial-gradient(ellipse 70% 40% at 30% 45%, var(--fuselage), transparent 75%),
      linear-gradient(180deg, rgba(14,14,16,.2) 0%, var(--rotor-black) 35%, var(--fuselage) 65%, rgba(14,14,16,.1) 100%);
  }
  .rotor-photo {
    position: absolute; left: 0; top: 250px; width: 420px; height: 60px; z-index: 1;
    background: linear-gradient(90deg, rgba(40,40,42,.9), rgba(60,60,62,.3) 80%, transparent);
    transform: rotate(-22deg); transform-origin: left center;
  }
  .brand {
    position: absolute; left: 0; right: 0; top: 66px;
    display: flex; justify-content: center; align-items: center; gap: 10px;
  }
  .brand-dot { width: 18px; height: 18px; border-radius: 50%; background: var(--magenta); }
  .brand-name { font-family: "Oswald", sans-serif; font-weight: 600; font-size: 30px; letter-spacing: .5px; color: var(--white); }
  .title { position: absolute; left: 0; right: 0; text-align: center; z-index: 3; }
  .title-main {
    top: 192px; font-family: "Chewy", "Luckiest Guy", sans-serif; font-size: 112px; line-height: 1;
    letter-spacing: 1px; color: var(--white);
    -webkit-text-stroke: 12px var(--violet); paint-order: stroke fill;
    text-shadow: 0 8px 0 var(--deep-violet);
  }
  .title-script {
    top: 282px; font-family: "Kaushan Script", cursive; font-size: 96px; line-height: 1;
    background: linear-gradient(180deg, var(--gold), var(--amber));
    -webkit-background-clip: text; background-clip: text; -webkit-text-fill-color: transparent;
    filter: drop-shadow(0 0 14px rgba(200,40,230,.8));
  }
  .heart-frame { position: absolute; left: 118px; top: 345px; width: 500px; height: 420px; z-index: 2; }
  .deco-heart { position: absolute; z-index: 4; }
  .offer { position: absolute; left: 0; right: 0; top: 560px; text-align: center; z-index: 4; }
  .offer-line { font-size: 20px; font-weight: 500; line-height: 28px; letter-spacing: .5px; }
  .offer-pill {
    display: inline-block; padding: 0 16px; margin: 1px 0; border-radius: 14px;
    background: linear-gradient(90deg, var(--violet), var(--magenta)); box-shadow: 0 0 0 2px rgba(255,255,255,.35);
  }
  .offer-sub { margin-top: 14px; font-size: 15px; line-height: 19px; font-weight: 500; letter-spacing: .5px; }
  .headline {
    position: absolute; left: 0; right: 0; top: 790px; text-align: center;
    font-size: 44px; font-weight: 600; letter-spacing: .5px; z-index: 4;
  }
  .headline-accent { color: var(--hot-pink); }
  .price-tag { position: absolute; left: 242px; top: 868px; width: 258px; height: 52px; z-index: 4; }
  .price-tag-label {
    position: absolute; inset: 0; display: flex; align-items: center; justify-content: center;
    font-size: 25px; font-weight: 600; padding-right: 16px;
  }
</style>
</head>
<body>
<div class="canvas">
  <div class="mailer">
    <div class="scene-photo" role="img" aria-label="Photo of a rocky riverbank below forested mountains at dusk"></div>
    <div class="rotor-photo" role="img" aria-label="Helicopter rotor blade crossing the sky"></div>
    <div class="helicopter-photo" role="img" aria-label="Photo of a black tour helicopter parked on the riverbank"></div>

    <div class="brand">
      <span class="brand-dot"></span>
      <span class="brand-name">Skylark Air Tours LLC</span>
    </div>

    <svg class="heart-frame" viewBox="0 0 510 430">
      <defs>
        <clipPath id="heart-clip">
          <path d="M255 420 C125 330 25 240 25 132 C25 52 95 12 165 22 C215 30 245 62 255 92 C265 62 295 30 345 22 C415 12 485 52 485 132 C485 240 385 330 255 420 Z"/>
        </clipPath>
        <linearGradient id="couple-tone" x1="0" y1="0" x2="0" y2="1">
          <stop offset="0" stop-color="#3c2a3a"/>
          <stop offset=".45" stop-color="#6a4a5c"/>
          <stop offset=".62" stop-color="#e07ad0"/>
          <stop offset="1" stop-color="#b0106e"/>
        </linearGradient>
      </defs>
      <g role="img" aria-label="Photo of a bride and groom embracing beside the helicopter">
        <rect width="510" height="430" fill="url(#couple-tone)" clip-path="url(#heart-clip)"/>
      </g>
      <path d="M255 420 C125 330 25 240 25 132 C25 52 95 12 165 22 C215 30 245 62 255 92 C265 62 295 30 345 22 C415 12 485 52 485 132 C485 240 385 330 255 420 Z"
            fill="none" stroke="var(--orchid)" stroke-width="18" stroke-linejoin="round"/>
    </svg>

    <div class="title title-main">HELICOPTER</div>
    <div class="title title-script">TOUR</div>

    <svg class="deco-heart" style="left:620px;top:340px;width:62px;height:56px" viewBox="0 0 100 90"><path d="M50 88 C20 65 2 45 2 25 C2 10 14 2 27 2 C38 2 46 9 50 18 C54 9 62 2 73 2 C86 2 98 10 98 25 C98 45 80 65 50 88 Z" fill="var(--hot-pink)"/></svg>
    <svg class="deco-heart" style="left:578px;top:362px;width:26px;height:24px" viewBox="0 0 100 90"><path d="M50 88 C20 65 2 45 2 25 C2 10 14 2 27 2 C38 2 46 9 50 18 C54 9 62 2 73 2 C86 2 98 10 98 25 C98 45 80 65 50 88 Z" fill="var(--violet)"/></svg>
    <svg class="deco-heart" style="left:256px;top:410px;width:22px;height:20px" viewBox="0 0 100 90"><path d="M50 88 C20 65 2 45 2 25 C2 10 14 2 27 2 C38 2 46 9 50 18 C54 9 62 2 73 2 C86 2 98 10 98 25 C98 45 80 65 50 88 Z" fill="var(--magenta)"/></svg>
    <svg class="deco-heart" style="left:214px;top:430px;width:34px;height:31px" viewBox="0 0 100 90"><path d="M50 88 C20 65 2 45 2 25 C2 10 14 2 27 2 C38 2 46 9 50 18 C54 9 62 2 73 2 C86 2 98 10 98 25 C98 45 80 65 50 88 Z" fill="var(--violet)"/></svg>
    <svg class="deco-heart" style="left:516px;top:542px;width:118px;height:106px" viewBox="0 0 100 90"><path d="M50 88 C20 65 2 45 2 25 C2 10 14 2 27 2 C38 2 46 9 50 18 C54 9 62 2 73 2 C86 2 98 10 98 25 C98 45 80 65 50 88 Z" fill="var(--hot-pink)"/></svg>

    <div class="offer">
      <div class="offer-line">THE ONLY</div>
      <div class="offer-line"><span class="offer-pill">VALENTINE’S DAY</span></div>
      <div class="offer-line">SURPRISE, YOU’LL NEED</div>
      <div class="offer-sub">ENJOY THE RIDE<br>WITH YOUR VALENTINE</div>
    </div>

    <div class="headline">AROUND <span class="headline-accent">VALENTINES</span> DAY</div>

    <div class="price-tag">
      <svg width="258" height="52" viewBox="0 0 258 52">
        <path d="M4 4 H226 L252 26 L226 48 H4 L12 26 Z" fill="var(--hot-pink)"/>
        <circle cx="236" cy="26" r="4" fill="var(--night)"/>
      </svg>
      <div class="price-tag-label">$169 PER PERSON</div>
    </div>
  </div>
</div>
</body>
</html>
```